Corvane Paintless Dent Removal

Our company works on vehicles removing dents using a highly skilled trade which the metal is massaged out with special tools without disturbing the original paint, hence paintless dent removal. Besides keeping the paint and metal original its also very environmentally friendly since no paint or toxic fillers are used. Also we we are one of the most experienced companies in the business with 25 years

Target Market(s)

Retail Automobile consumers, Auto Dealerships and Auto Body Shops

Industry/Entity Type

Auto Repair

Contact Information for Business Card

Dale Hollister
PO Box 518 Brookmere, NY 11962
631-555-0148
corvanepdr@mailbox-example.com
website corvanepdr.example
clipcast corvane paintless dent removal
25 years of experience removing Dents, Dings and Hail Damage

Font styles to use
Serif
Sans Serif

Colors

Designer to choose colors to be used in the design.

Requirements
Must have
• I do like things that are simple but classy and somewhat bold, also I like my logo so that should be somewhat important

```html
<!DOCTYPE html>
<html lang="en">
<head>
<meta charset="utf-8">
<title>Corvane Paintless Dent Removal – Business Card</title>
<link rel="stylesheet" href="https://fonts.googleapis.com/css2?family=Work+Sans:wght@400;500;600;700&display=swap">
<style>
  :root {
    --navy: #12284c;
    --green: #7dc242;
    --white: #ffffff;
    --backdrop: #1f1f21;
    --text-navy: #12284c;
  }
  * { box-sizing: border-box; margin: 0; padding: 0; }
  html, body { width: 1200px; height: 930px; overflow: hidden; }
  body {
    background: var(--backdrop);
    font-family: "Work Sans", Arial, sans-serif;
    position: relative;
  }
  .card {
    position: absolute;
    left: 278px;
    width: 645px;
    height: 368px;
    border-radius: 22px;
    overflow: hidden;
  }
  .card--front { top: 76px; background: var(--white); }
  .card--back { top: 486px; background: var(--navy); }

  .front-waves { position: absolute; inset: 0; width: 645px; height: 368px; }

  .holder {
    position: absolute;
    right: 37px;
    top: 52px;
    text-align: right;
  }
  .holder__name {
    font-size: 22px;
    font-weight: 600;
    letter-spacing: 1.2px;
    color: var(--text-navy);
    line-height: 1.1;
  }
  .holder__title {
    font-size: 16px;
    font-weight: 400;
    color: var(--green);
    margin-top: 2px;
  }
  .accent-bar {
    position: absolute;
    top: 54px;
    right: 0;
    height: 40px;
    width: 20px;
  }
  .accent-bar__line { position: absolute; left: 0; top: 0; width: 3px; height: 100%; background: var(--green); }
  .accent-bar__block { position: absolute; right: 0; top: 0; width: 16px; height: 100%; background: var(--navy); }

  .brand-front {
    position: absolute;
    left: 36px;
    top: 112px;
    width: 300px;
    font-size: 24px;
    font-weight: 700;
    line-height: 1.15;
    color: var(--navy);
    text-align: center;
  }

  .contact {
    position: absolute;
    right: 37px;
    top: 216px;
    text-align: right;
    color: var(--white);
    font-size: 16px;
    font-weight: 400;
    line-height: 20px;
  }
  .contact__address { margin-bottom: 14px; }
  .contact__row { display: flex; justify-content: flex-end; align-items: center; gap: 10px; }
  .contact__icon { width: 10px; height: 10px; flex: none; }

  .brand-back {
    position: absolute;
    left: 0; right: 0;
    top: 130px;
    text-align: center;
    font-size: 38px;
    font-weight: 700;
    line-height: 1.1;
    color: var(--white);
  }
  .back-info {
    position: absolute;
    left: 0; right: 0;
    top: 296px;
    text-align: center;
    color: var(--white);
    font-size: 16.5px;
    line-height: 21px;
  }
  .back-info__channel { color: var(--green); font-size: 22px; }
</style>
</head>
<body>

<section class="card card--front" aria-label="Business card front">
  <svg class="front-waves" viewBox="0 0 645 368" aria-hidden="true">
    <path d="M0,282 C150,340 320,270 430,200 C520,145 590,140 645,176 V368 H0 Z" fill="#12284c"/>
    <path d="M250,253 C380,190 470,120 560,100 C600,92 625,100 622,106 C585,96 540,110 470,150 C380,205 300,260 250,253 Z" fill="#12284c"/>
    <path d="M40,322 C180,335 330,250 440,185 C520,140 580,126 625,145" fill="none" stroke="#ffffff" stroke-width="5"/>
    <path d="M0,250 C90,292 230,270 322,208 C235,262 100,290 0,270 Z" fill="#7dc242"/>
  </svg>

  <div class="brand-front">Corvane<br>Paintless Dent Removal</div>

  <div class="holder">
    <div class="holder__name">DALE HOLLISTER</div>
    <div class="holder__title">President</div>
  </div>
  <div class="accent-bar"><span class="accent-bar__line"></span><span class="accent-bar__block"></span></div>

  <div class="contact">
    <div class="contact__address">PO Box 518<br>Brookmere, NY 11962</div>
    <div class="contact__row">631-555-0148
      <svg class="contact__icon" viewBox="0 0 10 10" aria-hidden="true"><path d="M2,1 L4,1 L4.5,3 L3.3,4 C4,5.5 4.8,6.4 6,7 L7,5.6 L9,6.2 L9,8.2 C5,8.8 1.2,5 2,1 Z" fill="#7dc242"/></svg>
    </div>
    <div class="contact__row">corvanepdr@mailbox-example.com
      <svg class="contact__icon" viewBox="0 0 10 10" aria-hidden="true"><rect x="0.8" y="2" width="8.4" height="6" fill="none" stroke="#7dc242" stroke-width="1.2"/><path d="M1,2.5 L5,5.5 L9,2.5" fill="none" stroke="#7dc242" stroke-width="1.1"/></svg>
    </div>
    <div class="contact__row">www.corvanepdr.example
      <svg class="contact__icon" viewBox="0 0 10 10" aria-hidden="true"><circle cx="5" cy="5" r="4" fill="none" stroke="#7dc242" stroke-width="1.1"/><path d="M1,5 H9 M5,1 C3,3.5 3,6.5 5,9 M5,1 C7,3.5 7,6.5 5,9" fill="none" stroke="#7dc242" stroke-width="0.9"/></svg>
    </div>
  </div>
</section>

<section class="card card--back" aria-label="Business card back">
  <div class="brand-back">Corvane<br>Paintless Dent Removal</div>
  <div class="back-info">
    <div><span class="back-info__channel">clipcast</span> corvane paintless dent removal</div>
    <div>25 years of experience removing Dents, Dings and Hail Damage</div>
  </div>
</section>

</body>
</html>
```